Expedition Cruise Sales Website for the Polar Regions (Antarctica & Arctic)

This will be a website for selling cruises.
This site should have a homepage, a ship page, destinations, and itineraries.
I have created a file specifying each page, and it is attached.
Pages:
1. Home
2. Cruise Lines
- 2.1 Ships
3. Destinations
- 3.1 Region - 3.2 Country - 3.3 City
4. Itineraries
- 4.1 Itinerary
5. Blog / Travel Tips 6. About Us
7. Contact
Please take a look on the attached pdf
Target Market(s)
Expedition Travelers
Coding
Coded - Design and coding required
Number of Pages Required
5+ page
Font styles to use
Look and feel
Each slider illustrates characteristics of the customer's brand and the style your logo design should communicate.

```html
<!DOCTYPE html>
<html lang="en">
<head>
<meta charset="UTF-8">
<title>Polarvue — Expedition Cruises</title>
<link href="https://fonts.googleapis.com/css2?family=Poppins:ital,wght@0,400;0,500;0,600;0,700;0,800;1,400&display=swap" rel="stylesheet">
<style>
:root{
  --page:#f4f4f6;
  --white:#ffffff;
  --ink:#141414;
  --muted:#6b6b72;
  --line:#e6e6ea;
  --field:#eef1f8;
  --pill:#f1f1f4;
  --blue:#2f6db5;
  --star:#e5673a;
}
*{box-sizing:border-box;margin:0;padding:0}
html,body{width:1200px;height:1200px;overflow:hidden}
body{background:var(--page);font-family:'Poppins',sans-serif;color:var(--ink);position:relative}
.abs{position:absolute}

/* cruise cards */
.cards-panel{left:137px;top:-40px;width:926px;height:265px;background:var(--white);border-radius:0 0 22px 22px}
.card{top:0;width:247px;height:222px;background:var(--white);border-radius:0 0 10px 10px;box-shadow:0 2px 10px rgba(0,0,0,.06);overflow:hidden}
.card-photo{position:absolute;left:0;top:0;width:100%;height:45px}
.card-title{position:absolute;left:14px;top:58px;font-size:16.5px;font-weight:500}
.card-rate{position:absolute;right:14px;top:62px;font-size:10px;color:var(--muted)}
.card-rule{position:absolute;left:14px;right:14px;height:1px;background:var(--line)}
.card-specs{position:absolute;left:14px;right:14px;top:103px;display:flex;justify-content:space-between;font-size:9px;color:var(--muted)}
.card-specs span{display:flex;align-items:center;gap:4px}
.card-desc{position:absolute;left:14px;right:12px;top:137px;font-size:9px;line-height:14px;color:#333;white-space:nowrap;overflow:hidden;text-overflow:ellipsis}
.card-desc p{overflow:hidden;text-overflow:ellipsis}
.card-price{position:absolute;left:14px;top:180px;font-size:17px;font-weight:600}
.btn-dark{background:var(--ink);color:var(--white);border-radius:999px;display:flex;align-items:center;justify-content:center;font-size:9.5px}
.card-btn{position:absolute;right:12px;top:177px;width:94px;height:29px}

/* home screen */
.home-panel{left:137px;top:322px;width:926px;height:606px;background:var(--white);border-radius:0 0 22px 22px;overflow:hidden}
.brand{left:16px;top:36px;display:flex;align-items:center;gap:6px;font-size:13px;font-weight:600;color:var(--blue)}
.brand i{display:block;width:10px;height:10px;border-radius:50%;background:var(--blue)}
.nav{left:105px;top:37px;display:flex;gap:0;font-size:11px}
.nav a{position:absolute;white-space:nowrap;color:var(--ink);text-decoration:none}
.nav a.active{font-weight:600}
.contact-btn{left:812px;top:30px;width:93px;height:30px;font-size:11px}
.search{left:17px;top:87px;width:444px;height:30px;background:var(--pill);border-radius:999px;display:flex;align-items:center;gap:8px;padding-left:16px;font-size:8.5px;color:#333}
.chip{top:87px;height:30px;border-radius:999px;background:var(--pill);display:flex;align-items:center;justify-content:center;gap:6px;font-size:8.5px;color:#333}
.chip.on{background:var(--ink);color:var(--white)}
.chip b{width:14px;height:14px;border-radius:50%;background:var(--white);display:inline-block}
.hero{left:16px;top:144px;width:893px;height:445px;border-radius:16px;overflow:hidden;
  background:linear-gradient(180deg,#5f7fa6 0%,#8aa2c0 40%,#a9b8cb 58%,#5a7694 70%,#3b5878 100%)}
.hero-ship{position:absolute;left:300px;top:30px;width:300px;height:335px;border-radius:40% 40% 10% 10%/20% 20% 8% 8%;background:linear-gradient(180deg,#dfe3ea,#c3c9d3 70%,#8c97a8)}
.hero-top{position:absolute;left:48px;right:30px;top:22px;display:flex;align-items:center;gap:10px;font-size:9px;color:var(--white)}
.hero-top hr{flex:1;border:0;height:1px;background:rgba(255,255,255,.8)}
.hero-title{position:absolute;left:0;right:0;top:160px;text-align:center;font-size:63px;font-weight:800;letter-spacing:1px;color:var(--white);text-shadow:0 2px 12px rgba(0,0,0,.2)}
.hero-sub{position:absolute;left:0;right:0;top:242px;text-align:center;font-size:10.5px;color:var(--white)}
.hero-btn{left:358px;top:293px;width:177px;height:35px;font-size:11px;font-weight:600}
.booking{left:54px;top:540px;width:817px;height:80px;background:var(--white);border-radius:8px 8px 0 0}
.field-label{position:absolute;top:17px;font-size:8.5px;color:var(--muted)}
.field{position:absolute;top:32px;width:198px;height:30px;background:var(--field);border-radius:4px;display:flex;align-items:center;gap:8px;padding-left:16px;font-size:8.5px}
.booking-btn{left:703px;top:26px;width:94px;height:29px;font-size:9.5px}

/* testimonial */
.review-panel{left:137px;top:1026px;width:926px;height:174px;background:var(--page)}
.review{left:77px;top:0;width:388px;height:174px;background:var(--white);overflow:hidden}
.quote{position:absolute;left:29px;top:-12px;width:328px;font-size:11px;line-height:17.5px;font-style:italic;text-align:justify;color:#222}
.quote-mark{position:absolute;left:343px;top:76px;font-size:44px;font-weight:800;color:var(--blue);line-height:1}
.avatar{position:absolute;left:25px;top:114px;width:38px;height:38px;border-radius:50%;background:linear-gradient(135deg,#c9b9a8,#8d7766)}
.reviewer{position:absolute;left:73px;top:116px;font-size:12px;font-weight:600}
.verified{position:absolute;left:73px;top:134px;font-size:9.5px;font-style:italic;color:#444}
.stars{position:absolute;left:72px;top:149px;display:flex;gap:3px}
.circle-btn{position:absolute;width:26px;height:26px;border-radius:50%;display:flex;align-items:center;justify-content:center}
.circle-btn.ghost{background:#f0f0f2}
.circle-btn.solid{background:var(--blue)}
.gallery{left:477px;top:0;width:449px;height:174px;background:var(--white)}
.gallery-main{position:absolute;left:23px;top:0;width:324px;height:105px;border-radius:0 0 10px 10px;background:linear-gradient(160deg,#9fb3c6,#e9edf1 55%,#b9a99a)}
.thumb{position:absolute;top:123px;width:46px;height:45px;border-radius:6px}
</style>
</head>
<body>

<!-- cruise cards -->
<section class="abs cards-panel" aria-label="Featured cruises">
  <article class="abs card" style="left:77px">
    <div class="card-photo" role="img" aria-label="Icy Antarctic waters" style="background:linear-gradient(180deg,#6f7f8e,#a6b2bc)"></div>
    <h3 class="card-title">Best Antarctic Cruises</h3>
    <span class="card-rate">★ 4.8</span>
    <div class="card-rule" style="top:92px"></div>
    <div class="card-specs"><span>⤡ 85" ft</span><span>👥 6 Guest</span><span>☺ 5 Crew</span></div>
    <div class="card-rule" style="top:124px"></div>
    <div class="card-desc"><p>Experience the untouched beauty of Antarctica.</p><p>Navigate through massive glaciers and icebergs...</p></div>
    <div class="card-price">$4,499</div>
    <div class="btn-dark card-btn">Book Now</div>
  </article>
  <article class="abs card" style="left:340px">
    <div class="card-photo" role="img" aria-label="Yacht on turquoise water" style="background:linear-gradient(180deg,#3bb6c0,#1e8f9b)"></div>
    <h3 class="card-title">Top Galápagos Cruises</h3>
    <span class="card-rate">★ 4.8</span>
    <div class="card-rule" style="top:92px"></div>
    <div class="card-specs"><span>⤡ 85" ft</span><span>👥 6 Guest</span><span>☺ 5 Crew</span></div>
    <div class="card-rule" style="top:124px"></div>
    <div class="card-desc"><p>Discover nature's masterpiece with a luxury</p><p>cruise to the Galápagos Islands. Explore rare wildlife...</p></div>
    <div class="card-price">$2,999</div>
    <div class="btn-dark card-btn">Book Now</div>
  </article>
  <article class="abs card" style="left:602px">
    <div class="card-photo" role="img" aria-label="Wooden pier by the sea" style="background:linear-gradient(180deg,#7e96ad,#a88869)"></div>
    <h3 class="card-title">Last-Minute Deals</h3>
    <div class="card-rule" style="top:92px"></div>
    <div class="card-specs"><span>⤡ 85" ft</span><span>👥 6 Guest</span><span>☺ 5 Crew</span></div>
    <div class="card-rule" style="top:124px"></div>
    <div class="card-desc"><p>Don't miss out! Book your next adventure at a</p><p>discounted rate with our exclusive last-minute deals.</p></div>
    <div class="card-price">$1,889</div>
    <div class="btn-dark card-btn">Grab the Deal</div>
  </article>
</section>

<!-- home screen -->
<section class="abs home-panel" aria-label="Home page">
  <div class="abs brand"><i></i>Polarvue</div>
  <nav class="abs nav">
    <a class="active" style="left:0">Home</a>
    <a style="left:59px">Cruise Lines</a>
    <a style="left:149px">Destinations</a>
    <a style="left:241px">Itineraries</a>
    <a style="left:321px">Blog</a>
    <a style="left:372px">About Us</a>
  </nav>
  <div class="abs btn-dark contact-btn">Contact</div>

  <div class="abs search">
    <svg width="10" height="10" viewBox="0 0 10 10"><circle cx="4.2" cy="4.2" r="3" fill="none" stroke="#333" stroke-width="1.2"/><path d="M6.5 6.5 9 9" stroke="#333" stroke-width="1.2"/></svg>
    Search Cruise Destination
  </div>
  <div class="abs chip on" style="left:482px;width:103px"><b></b>Departure date</div>
  <div class="abs chip" style="left:601px;width:92px">⌂ Cruise Length</div>
  <div class="abs chip" style="left:709px;width:91px">⌂ Departure port</div>
  <div class="abs chip" style="left:816px;width:90px">⌂ Cruise Line</div>

  <div class="abs hero">
    <div class="hero-ship" role="img" aria-label="Large cruise ship at sea"></div>
    <div class="hero-top"><span>Special Offers Available!</span><hr><span>January 2025 - April 2025</span></div>
    <h1 class="hero-title">LUXURY AWAITS YOU</h1>
    <p class="hero-sub">Explore the world's best destinations aboard the finest ships. Book your dream cruise today.</p>
    <div class="abs btn-dark hero-btn">Start Your Journey</div>
  </div>

  <div class="abs booking">
    <span class="field-label" style="left:19px">Cruising to</span>
    <div class="field" style="left:19px">⌂ Anywhere</div>
    <span class="field-label" style="left:248px">Date</span>
    <div class="field" style="left:248px;width:196px">▦ Select Date</div>
    <span class="field-label" style="left:475px">Guest</span>
    <div class="field" style="left:475px">👥 Select Guest<span style="margin-left:auto;margin-right:18px">▾</span></div>
    <div class="abs btn-dark booking-btn">Search Cruise</div>
  </div>
</section>

<!-- testimonial -->
<section class="abs review-panel" aria-label="Traveler reviews">
  <div class="abs review">
    <p class="quote">The Mediterranean cruise was everything I dreamed of and more. We visited some of the most beautiful ports, and the luxurious accommodations made it feel like a five-star resort on the water. The staff went above and beyond to make every moment special. I've already booked my next cruise!</p>
    <div class="quote-mark">”</div>
    <div class="avatar" role="img" aria-label="Reviewer portrait"></div>
    <div class="reviewer">Maren T</div>
    <div class="verified">Verified Traveler</div>
    <div class="stars">
      <svg width="70" height="12" viewBox="0 0 70 12" fill="var(--star)">
        <path d="M6 0l1.8 3.9 4.2.5-3.1 2.9.8 4.2L6 9.4 2.3 11.5l.8-4.2L0 4.4l4.2-.5z"/>
        <path transform="translate(14.5 0)" d="M6 0l1.8 3.9 4.2.5-3.1 2.9.8 4.2L6 9.4 2.3 11.5l.8-4.2L0 4.4l4.2-.5z"/>
        <path transform="translate(29 0)" d="M6 0l1.8 3.9 4.2.5-3.1 2.9.8 4.2L6 9.4 2.3 11.5l.8-4.2L0 4.4l4.2-.5z"/>
        <path transform="translate(43.5 0)" d="M6 0l1.8 3.9 4.2.5-3.1 2.9.8 4.2L6 9.4 2.3 11.5l.8-4.2L0 4.4l4.2-.5z"/>
        <path transform="translate(58 0)" d="M6 0l1.8 3.9 4.2.5-3.1 2.9.8 4.2L6 9.4 2.3 11.5l.8-4.2L0 4.4l4.2-.5z"/>
      </svg>
    </div>
    <div class="circle-btn ghost" style="left:300px;top:124px"><svg width="8" height="10" viewBox="0 0 8 10"><path d="M6 1 2 5l4 4" fill="none" stroke="#888" stroke-width="1.4"/></svg></div>
    <div class="circle-btn solid" style="left:338px;top:124px"><svg width="8" height="10" viewBox="0 0 8 10"><path d="M2 1l4 4-4 4" fill="none" stroke="#fff" stroke-width="1.6"/></svg></div>
  </div>

  <div class="abs gallery">
    <div class="gallery-main" role="img" aria-label="Traveler standing on a sailing boat deck"></div>
    <div class="circle-btn ghost" style="left:23px;top:132px"><svg width="8" height="10" viewBox="0 0 8 10"><path d="M6 1 2 5l4 4" fill="none" stroke="#888" stroke-width="1.4"/></svg></div>
    <div class="thumb" role="img" aria-label="Deck scene" style="left:65px;background:linear-gradient(135deg,#8a6c58,#d8cfc6)"></div>
    <div class="thumb" role="img" aria-label="Cabin scene" style="left:124px;background:linear-gradient(135deg,#5b2d2a,#c9b7ad)"></div>
    <div class="thumb" role="img" aria-label="Sea view" style="left:184px;background:linear-gradient(135deg,#9fb7cc,#e6e1da)"></div>
    <div class="thumb" role="img" aria-label="Coastline view" style="left:243px;background:linear-gradient(135deg,#6f9bc4,#dfe6ee)"></div>
    <div class="circle-btn solid" style="left:283px;top:132px"><svg width="8" height="10" viewBox="0 0 8 10"><path d="M2 1l4 4-4 4" fill="none" stroke="#fff" stroke-width="1.6"/></svg></div>
  </div>
</section>

</body>
</html>
```